RW Holloway LLC Business Card - Civil Engineering & Consulting Firm

We need a Business Card that is elegant, and masculine.  It is our Professional Civil Engineering & Consulting Company located in San Antonio TX (Not s construction or builder firm- no gears & no tool images please). We provide civil engineering services including  commercial site plans, grading and drainage plans, utility plans, hydraulics and hydrology, land planning, utility coordination, and other general civil engineering services related to commercial and residential development.
We have 2 existing Logos. We would like to convey reliability, strength, trustworthiness and attention to detail.  Blues and orange tones as per logo We are OK with the use of a darker blue in the mix.  We have 2 logo versions - Full Company Name Logo to go on the back of card, & Small Icon Logo for the front w/ personal Info.

Target Market(s)
Architects, Real Estate Developers, Other Strctural Engineers, Surveyers, General Contractors
Industry/Entity Type
Professional Civil Engineering
Contact Information for Business Card
Name, Position, Address, Cell & Office #, email, and company website
Font styles to use
Other font styles liked:
- Avian
Requirements
Should not have
- No Tools, No Gears, no Cranes, or Construction Equipment.

```html
<!DOCTYPE html>
<html lang="en">
<head>
<meta charset="utf-8">
<title>RW Holloway LLC – Business Card</title>
<link rel="stylesheet" href="https://fonts.googleapis.com/css2?family=Montserrat:wght@300;400;600;700&display=swap">
<style>
  :root {
    --page: #c9c9c9;
    --card-white: #ffffff;
    --card-grey: #efedee;
    --orange: #ee8f2c;
    --blue: #7aaed8;
    --steel: #7c9fbf;
    --ink: #1d1d1d;
    --light: #ffffff;
  }
  * { margin: 0; padding: 0; box-sizing: border-box; }
  html, body { width: 1200px; height: 813px; overflow: hidden; }
  body {
    background: var(--page);
    font-family: "Montserrat", Arial, sans-serif;
    display: flex;
    align-items: center;
    justify-content: center;
    gap: 40px;
  }
  .card {
    position: relative;
    width: 540px;
    height: 292px;
    overflow: hidden;
    box-shadow: 0 6px 18px rgba(0,0,0,.25);
  }

  /* Front */
  .card-front {
    background: linear-gradient(110deg, var(--card-white) 45%, var(--card-grey) 100%);
  }
  .front-stripe {
    position: absolute;
    left: 0; right: 0;
    bottom: 50px;
    height: 3px;
    background: var(--blue);
  }
  .front-band {
    position: absolute;
    left: 0; right: 0; bottom: 0;
    height: 44px;
    background: linear-gradient(90deg, var(--blue) 0%, var(--blue) 22%, #b5a48f 50%, var(--orange) 85%);
  }
  .front-brand {
    position: absolute;
    top: 62px;
    right: 56px;
    display: flex;
    align-items: center;
    gap: 10px;
    font-weight: 600;
    font-size: 22px;
    color: var(--orange);
  }
  .front-brand .mark { width: 14px; height: 14px; background: var(--blue); }
  .contact {
    position: absolute;
    left: 30px;
    top: 84px;
    color: var(--ink);
    font-size: 11.5px;
    line-height: 1.4;
  }
  .contact .name {
    color: var(--orange);
    font-weight: 700;
    font-size: 17px;
    letter-spacing: .5px;
    line-height: 1.2;
  }
  .contact .role { font-size: 12px; margin-bottom: 7px; }
  .contact .address { margin-bottom: 7px; }
  .contact-line { display: flex; align-items: center; gap: 8px; }
  .contact-line svg { width: 11px; height: 11px; flex: none; }

  /* Back */
  .card-back {
    background: linear-gradient(160deg, var(--steel) 0%, #a7968a 45%, var(--orange) 100%);
    color: var(--light);
    display: flex;
    flex-direction: column;
    align-items: center;
    justify-content: center;
    gap: 14px;
  }
  .back-name {
    font-weight: 300;
    font-size: 40px;
    letter-spacing: 3px;
  }
  .back-rule { width: 380px; height: 2px; background: var(--light); }
  .back-tagline {
    font-weight: 300;
    font-size: 14px;
    letter-spacing: 7px;
    text-transform: uppercase;
  }
</style>
</head>
<body>
  <section class="card card-front">
    <div class="front-stripe"></div>
    <div class="front-band"></div>
    <div class="front-brand"><span class="mark"></span>RW Holloway LLC</div>
    <div class="contact">
      <div class="name">DANE WHITLOCK</div>
      <div class="role">Co-Founder</div>
      <div class="address">4180 N. Cedar Ridge Road<br>Suite 210 Bexar 78</div>
      <div class="contact-line">
        <svg viewBox="0 0 12 12"><path d="M2 1h3l1 3-2 1a6 6 0 0 0 3 3l1-2 3 1v3c-6 1-10-3-9-9z" fill="var(--orange)"/></svg>555-214-0381
      </div>
      <div class="contact-line">
        <svg viewBox="0 0 12 12"><rect x="1" y="4" width="10" height="7" rx="1" fill="var(--orange)"/><rect x="2" y="1" width="8" height="3" rx="1" fill="var(--orange)"/></svg>555-214-0392
      </div>
      <div class="contact-line">
        <svg viewBox="0 0 12 12"><rect x="0.5" y="2" width="11" height="8" fill="var(--orange)"/><path d="M1 2.5l5 4 5-4" stroke="#fff" fill="none"/></svg>info@rwholloway
      </div>
      <div class="contact-line">
        <svg viewBox="0 0 12 12"><circle cx="6" cy="6" r="5.5" fill="var(--orange)"/><path d="M1 6h10M6 .5v11" stroke="#fff" stroke-width=".8"/></svg>www.hollowayeng.com
      </div>
    </div>
  </section>

  <section class="card card-back">
    <div class="back-name">RW Holloway LLC</div>
    <div class="back-rule"></div>
    <div class="back-tagline">Consulting Engineers</div>
  </section>
</body>
</html>
```